New Business Card Design for Manufacturing

We are an engineering/manufacturing company that offers Advanced machining/assembly/engineering services, as well as innovative products for the heavy duty engine cooling markets.

We are looking to get a new business card designed that is clean and modern looking, but still fits the wide range of technical/skilled work we do.

- We hope to use this design as the base for other design work in new Presentations, web, and print work.

Industry/Entity Type

Engineering

Contact Information for Business Card

Our preferred color of blue is (RGB) 22/71/159 but can vary slightly from that color. Our content will be our Logo and full company name (Vantrell Forge Works, Inc.), company address, name, job title, phone number with extension, cell number, fax number, website, and email address on the cards.
We'd like the full company name next to the logo, but we are open to other interpretations of that layout.
Preferably, we would like the back side to be clean with just our logo, and the front to contain all of the contact information.

Colors
2f74b4
0355a3
85abd2

Requirements
Must have
• - Logo, company name, needed content - We are open to interpretation beyond that.
• - Standard size business card.
• - Horizontal orientation.
• - Enough space for lengthy names / job titles (for example, a job title could read "Directory of Human Resources" or "V.P. of Governmental Affairs"). We need this to look clean, whether the title be short (CEO) or long (as described above).

```html
<!DOCTYPE html>
<html lang="en">
<head>
<meta charset="utf-8">
<title>Vantrell Forge Works – Business Card</title>
<link rel="stylesheet" href="https://fonts.googleapis.com/css2?family=Cabin:wght@500;600&family=Open+Sans:wght@400;800&display=swap">
<style>
  :root {
    --brand-blue: #0355a3;
    --ink-blue: #16479f;
    --light-blue: #85abd2;
    --page: #e4e4e4;
    --card-white: #f7f7f7;
    --text-grey: #3c3c3c;
    --band-grey: #8a8d91;
    --white: #ffffff;
  }
  * { margin: 0; padding: 0; box-sizing: border-box; }
  html, body {
    width: 1200px; height: 576px; overflow: hidden;
    background: var(--page);
    font-family: "Open Sans", Arial, sans-serif;
  }
  .canvas { position: relative; width: 1200px; height: 576px; }

  .card {
    position: absolute; top: 138px;
    width: 484px; height: 294px;
    border-radius: 14px; overflow: hidden;
  }

  /* Back side */
  .card-back { left: 82px; background: var(--brand-blue); }
  .card-back .wordmark {
    position: absolute; left: 0; right: 0; top: 110px;
    text-align: center;
    font-family: "Open Sans", Arial, sans-serif;
    font-weight: 800; font-size: 58px; letter-spacing: 2px;
    color: var(--white); line-height: 1;
  }
  .card-back .web-row {
    position: absolute; left: 0; right: 0; top: 264px;
    display: flex; justify-content: center; align-items: center; gap: 10px;
    color: var(--white); font-size: 13px;
  }
  .card-back .rule { width: 52px; height: 2px; background: var(--white); border-radius: 1px; }

  /* Front side */
  .card-front { left: 603px; background: var(--card-white); }
  .card-front .wordmark {
    position: absolute; right: 24px; top: 34px;
    font-weight: 800; font-size: 52px; letter-spacing: 2px;
    color: var(--brand-blue); line-height: 1;
  }
  .person-name {
    position: absolute; left: 22px; top: 142px;
    font-family: "Cabin", Arial, sans-serif; font-weight: 500;
    font-size: 21px; color: var(--ink-blue);
  }
  .person-title {
    position: absolute; left: 22px; top: 170px;
    font-size: 12px; color: var(--text-grey);
  }
  .title-rule {
    position: absolute; left: 132px; right: 22px; top: 183px;
    height: 1px; background: var(--ink-blue);
  }
  .company-name {
    position: absolute; right: 24px; top: 194px;
    font-family: "Cabin", Arial, sans-serif; font-weight: 600;
    font-size: 14.5px; color: var(--ink-blue);
  }
  .address {
    position: absolute; right: 24px; top: 218px;
    text-align: right; font-size: 13px; line-height: 18px; color: var(--text-grey);
  }
  .contact-list { position: absolute; left: 24px; top: 200px; list-style: none; }
  .contact-list li {
    display: flex; align-items: center; gap: 8px;
    height: 17.6px; font-size: 12.5px; color: var(--text-grey);
  }
  .contact-list svg { width: 11px; height: 11px; fill: var(--ink-blue); flex: none; }
  .footer-band { position: absolute; left: 0; bottom: 0; width: 484px; height: 32px; }
  .footer-web {
    position: absolute; right: 24px; bottom: 7px;
    font-size: 13px; color: var(--white);
  }
</style>
</head>
<body>
<div class="canvas">

  <section class="card card-back" aria-label="Card back">
    <div class="wordmark">VANTRELL</div>
    <div class="web-row">
      <span class="rule"></span>
      <span>www.vantrellforge.com</span>
      <span class="rule"></span>
    </div>
  </section>

  <section class="card card-front" aria-label="Card front">
    <div class="wordmark">VANTRELL</div>

    <div class="person-name">Marcus Ellery Hale</div>
    <div class="person-title">Managing Director</div>
    <div class="title-rule"></div>

    <ul class="contact-list">
      <li>
        <svg viewBox="0 0 12 12" aria-hidden="true"><path d="M1 4c0-2 2-3 5-3s5 1 5 3v1H8.5V3.8h-5V5H1zM3 6h6l1.5 5h-9z"/></svg>
        616-555-0142 (ext. 214)
      </li>
      <li>
        <svg viewBox="0 0 12 12" aria-hidden="true"><path d="M3 0h6a1 1 0 0 1 1 1v10a1 1 0 0 1-1 1H3a1 1 0 0 1-1-1V1a1 1 0 0 1 1-1zm.5 1.5v7h5v-7zM6 9.3a.8.8 0 1 0 0 1.6.8.8 0 0 0 0-1.6z"/></svg>
        616-555-0187
      </li>
      <li>
        <svg viewBox="0 0 12 12" aria-hidden="true"><path d="M3 0h6v3H3zM1 4h10a1 1 0 0 1 1 1v4H9.5v3h-7V9H0V5a1 1 0 0 1 1-1zm2.5 4v3h5V8z"/></svg>
        616-555-0199
      </li>
      <li>
        <svg viewBox="0 0 12 12" aria-hidden="true"><path d="M0 2h12v.8L6 6.6 0 2.8zM0 4l6 3.8L12 4v6H0z"/></svg>
        m.hale@vantrellforge.com
      </li>
    </ul>

    <div class="company-name">Vantrell Forge Works, Inc.</div>
    <div class="address">418 Foundry Row, Millbrook,<br>Lakeside, US 482190</div>

    <svg class="footer-band" viewBox="0 0 484 32" aria-hidden="true">
      <rect x="0" y="18" width="484" height="14" fill="var(--band-grey)"/>
      <path d="M226 32 L244 2 Q245 0 248 0 H484 V32 Z" fill="var(--brand-blue)"/>
    </svg>
    <div class="footer-web">www.vantrellforge.com</div>
  </section>

</div>
</body>
</html>
```